Wordpress template for a mens-choire webpage

Task is to design a Wordpress template for an 98 years old estonian mens choire webpage.
Design should involve details from the attached files, choire logo and the colors of the choire flag: in horizontal orientation bright sky-blue, white, bright grass-green.
Designer signature is allowed to be added to the template, with country of origin.

Reason: Deadline extended 2 days (until 2. March 2014) to accommodate designers creativity.

Thank you everyone for your great designs!
Our project has now entered into a voting and decision phase until 14th of March 2014 (included).

```html
<!DOCTYPE html>
<html lang="en">
<head>
<meta charset="utf-8">
<title>Valgemere Meeskoor</title>
<link rel="stylesheet" href="https://fonts.googleapis.com/css2?family=Open+Sans:wght@400;600&family=Roboto:wght@400;500&display=swap">
<style>
:root{
  --sky:#0a82c8;
  --grass:#1f8a22;
  --grass-dark:#0d5a10;
  --paper:#ffffff;
  --accent:#a30a0a;
  --ink:#555555;
  --ink-soft:#6a6a6a;
  --rule:#cfcfcf;
  --photo-dark:#3a332d;
}
*{margin:0;padding:0;box-sizing:border-box}
html,body{width:987px;height:1200px;overflow:hidden}
body{position:relative;font-family:"Open Sans",Arial,sans-serif;color:var(--ink);background:var(--sky)}
.backdrop{position:absolute;inset:0}
.sheet{position:absolute;left:131px;top:31px;width:720px;height:1114px;background:var(--paper);box-shadow:0 3px 10px rgba(0,0,0,.25)}
.brand{position:absolute;left:16px;top:30px;display:flex;align-items:center;gap:8px}
.brand-dot{width:26px;height:26px;border-radius:50%;background:var(--accent)}
.brand-name{font-family:"Roboto",Arial,sans-serif;font-weight:500;font-size:16px;color:var(--accent);line-height:1.1}
.phone{position:absolute;right:16px;top:47px;display:flex;align-items:center;gap:9px;font-family:"Roboto",Arial,sans-serif;font-size:15px;color:var(--ink-soft)}
.nav{position:absolute;right:16px;top:95px;display:flex;list-style:none}
.nav li{font-family:"Roboto",Arial,sans-serif;font-size:12.5px;color:#444;height:29px;line-height:29px;padding:0 14px}
.nav li:last-child{padding-right:0}
.nav li.current{background:var(--accent);color:#fff}
.slider{position:absolute;left:16px;top:157px;width:687px;height:325px;background:linear-gradient(180deg,#6f6458 0%,#4a403a 45%,#1e1a18 100%)}
.slider-caption{position:absolute;left:0;right:0;bottom:0;height:39px;background:rgba(0,0,0,.55);color:#fff;text-align:center;font-family:"Roboto",Arial,sans-serif;font-size:19.5px;line-height:39px}
.slider-shade{position:absolute;left:16px;top:482px;width:687px;height:32px}
.dots{position:absolute;left:335px;top:511px;display:flex;gap:2px}
.dots span{width:14px;height:14px;border-radius:50%;background:#d4d4d4;box-shadow:inset 0 0 0 2px #eee,0 0 1px #999}
.dots span.on{background:#6a6a6a}
.tiles{position:absolute;left:15px;top:555px;width:688px;height:133px}
.tile{position:absolute;top:0;width:210px;height:133px}
.tile-bar{position:absolute;left:0;right:0;bottom:0;height:30px;background:rgba(0,0,0,.55);color:#fff;font-family:"Open Sans",Arial,sans-serif;font-size:12px;line-height:30px;padding-left:11px}
.tile-bar svg{position:absolute;right:11px;top:8px}
.welcome{position:absolute;left:16px;top:733px;width:403px}
h2{font-family:"Open Sans",Arial,sans-serif;font-weight:400;font-size:20px;color:var(--accent)}
.welcome p{font-size:9.6px;line-height:16.4px;color:var(--ink-soft);margin-top:8px}
.welcome h2{margin-bottom:16px}
.events{position:absolute;left:478px;top:733px;width:226px}
.events h2{margin-bottom:14px}
.event{display:flex;gap:6px;margin-bottom:17px}
.event-thumb{width:68px;height:46px;flex:none}
.event h3{font-family:"Open Sans",Arial,sans-serif;font-weight:400;font-size:10px;color:var(--accent);margin-top:-2px;margin-bottom:4px}
.event p{font-size:8.8px;line-height:15.6px;color:var(--ink-soft)}
.footer-rule{position:absolute;left:16px;top:1008px;width:687px;border-top:1px solid var(--rule)}
.footer-links{position:absolute;left:22px;top:1040px;font-family:"Roboto",Arial,sans-serif;font-size:10px;color:#444}
.footer-links span{margin:0 8px}
.copyright{position:absolute;left:22px;top:1066px;font-family:"Roboto",Arial,sans-serif;font-size:10px;color:#444}
.social{position:absolute;left:519px;top:1044px;display:flex;gap:9px}
.social span{width:25px;height:25px}
</style>
</head>
<body>
<svg class="backdrop" width="987" height="1200" viewBox="0 0 987 1200" aria-hidden="true">
  <defs>
    <linearGradient id="grass" x1="0" y1="0" x2="0" y2="1">
      <stop offset="0" stop-color="var(--grass)"/>
      <stop offset="1" stop-color="var(--grass-dark)"/>
    </linearGradient>
  </defs>
  <rect width="987" height="1200" fill="var(--sky)"/>
  <path d="M0 0H987V510C760 530 420 520 0 565Z" fill="#fff"/>
  <path d="M0 0H987V220C760 222 300 170 0 196Z" fill="url(#grass)"/>
</svg>

<main class="sheet">
  <div class="brand">
    <span class="brand-dot"></span>
    <span class="brand-name">Valgemere<br>Meeskoor</span>
  </div>

  <div class="phone">
    <svg width="22" height="22" viewBox="0 0 24 24"><path d="M6.6 10.8a15 15 0 0 0 6.6 6.6l2.2-2.2c.3-.3.7-.4 1-.2 1.1.4 2.3.6 3.6.6.6 0 1 .4 1 1V20c0 .6-.4 1-1 1A17 17 0 0 1 3 4c0-.6.4-1 1-1h3.5c.6 0 1 .4 1 1 0 1.3.2 2.5.6 3.6.1.3 0 .7-.2 1Z" fill="#777"/></svg>
    <span>372 555 0148 20</span>
  </div>

  <ul class="nav">
    <li class="current">HOME</li>
    <li>ABOUT US</li>
    <li>SERVICES</li>
    <li>BLOG</li>
    <li>CONTACT</li>
  </ul>

  <div class="slider" role="img" aria-label="Photo of the men's choir in dark traditional costumes standing on stone steps before an old archway">
    <div class="slider-caption">98 Years of Estonian Choire</div>
  </div>
  <svg class="slider-shade" viewBox="0 0 687 32" preserveAspectRatio="none" aria-hidden="true">
    <defs>
      <linearGradient id="shade" x1="0" y1="0" x2="1" y2="0">
        <stop offset="0" stop-color="#fff"/>
        <stop offset=".3" stop-color="#9a9a9a"/>
        <stop offset=".5" stop-color="#ffffff"/>
        <stop offset=".7" stop-color="#9a9a9a"/>
        <stop offset="1" stop-color="#fff"/>
      </linearGradient>
    </defs>
    <path d="M0 0H687C560 32 127 32 0 0Z" fill="url(#shade)"/>
  </svg>
  <div class="dots"><span class="on"></span><span></span><span></span><span></span></div>

  <section class="tiles">
    <div class="tile" style="left:0;background:linear-gradient(180deg,#8a8a8a,#2b2b2b)" role="img" aria-label="Photo of a collegiate choir in black suits">
      <div class="tile-bar">Collegiate Choirs<svg width="14" height="14" viewBox="0 0 14 14"><circle cx="7" cy="7" r="7" fill="#fff"/><path d="M3.5 7H9M7 4.5 9.5 7 7 9.5" stroke="#222" stroke-width="1.6" fill="none"/></svg></div>
    </div>
    <div class="tile" style="left:241px;background:linear-gradient(180deg,#3c3c3c,#0c0c0c)" role="img" aria-label="Photo of a school choir performing on stage">
      <div class="tile-bar">School Choirs<svg width="14" height="14" viewBox="0 0 14 14"><circle cx="7" cy="7" r="7" fill="#fff"/><path d="M3.5 7H9M7 4.5 9.5 7 7 9.5" stroke="#222" stroke-width="1.6" fill="none"/></svg></div>
    </div>
    <div class="tile" style="left:478px;background:linear-gradient(180deg,#c9ccd8,#2a2628)" role="img" aria-label="Photo of a community choir in front of church windows">
      <div class="tile-bar">Community Choirs<svg width="14" height="14" viewBox="0 0 14 14"><circle cx="7" cy="7" r="7" fill="#fff"/><path d="M3.5 7H9M7 4.5 9.5 7 7 9.5" stroke="#222" stroke-width="1.6" fill="none"/></svg></div>
    </div>
  </section>

  <section class="welcome">
    <h2>Welcome to Our Website</h2>
    <p>Eu tortor euismodolo. Vestibulum ant psu meop primis inicibu orci luctus ed ultrices et posuere cubil. Cura sed quis nibhut odiocinialor matis ed iaculis ante sed vel laciniate. Eu tortor euismodolo. Vestibulum ant psu meop primis inicibu orci luctus ed ultrices et posuere cubl. Cura sed quis nibhut odiocinialor matis ed iaculis ante sed vel laciniate.</p>
    <p>Eu tortor euismodolo. Vestibulum ant psu meop primis inicibu orci luctus ed ultrices et posuere cubil. Cura sed quis nibhut odiocinialor matis ed iaculis ante sed vel laciniate. Eu tortor euismodolo. Vestibulum ant psu meop primis inicibu orci luctus ed ultrices et posuere cubil. Cura sed quis nibhut odiocinialor matis ed iaculis ante sed vel laciniate. Eu tortor euismodolo. Vestibulum ant psu meop primis inicibu orci luctus ed ultrices et posuere cubil. Cura sed quis nibhut odiocinialor matis ed iaculis ante sed vel laciniate. Eu tortor euismodolo.</p>
  </section>

  <aside class="events">
    <h2>Upcoming Events</h2>
    <div class="event">
      <div class="event-thumb" style="background:linear-gradient(180deg,#8b8fa0,#2a2a30)" role="img" aria-label="Photo of a choir in a church hall"></div>
      <div><h3>Duis autem vel eum iriure dolor</h3><p>Brianne craves the endorphin rush fueled by fitness and uses it.</p></div>
    </div>
    <div class="event">
      <div class="event-thumb" style="background:linear-gradient(180deg,#b4b4b4,#2e2e2e)" role="img" aria-label="Photo of singers in dark suits"></div>
      <div><h3>Duis autem vel eum iriure dolor</h3><p>Brianne craves the enindorphin rush fueled by fitness and uses it.</p></div>
    </div>
    <div class="event">
      <div class="event-thumb" style="background:linear-gradient(180deg,#6a5a48,#1a1512)" role="img" aria-label="Photo of a large choir on a concert stage"></div>
      <div><h3>Duis autem vel eum iriure dolor</h3><p>Brianne craves the enindorphin rush fueled by fitness and uses it.</p></div>
    </div>
  </aside>

  <div class="footer-rule"></div>
  <div class="footer-links">Terms and Conditions<span>|</span>Privacy Policy<span>|</span>Sitemap</div>
  <div class="copyright">© 2013 Copyrights Reserved. All rights reserved.</div>
  <div class="social" aria-label="Social links">
    <span style="background:#2f4f9e"></span>
    <span style="background:#1e8fd0"></span>
    <span style="background:#f26a16"></span>
    <span style="background:#d21a1a"></span>
    <span style="background:#7cc4ea"></span>
  </div>
</main>
</body>
</html>
```